Business Card Design Project

I require a business card with the following information on them for various different people;
name
m:
f:
e:
I have a logo already and will attached that. We are in the construction industry. I require something clean and simple but eye catching at the same time. You can use another colour with our logo if you like and you can style the logo as well if you wish. I am open.
Also it needs to be front and back design.
Industry/Entity Type
Construction
Requirements
Must have
- Logo, name, mobile, fax and email address.
Front and back design

```html
<!DOCTYPE html>
<html lang="en">
<head>
<meta charset="UTF-8">
<title>Stonefield Developments – Business Cards</title>
<link href="https://fonts.googleapis.com/css2?family=Open+Sans:wght@400;600&display=swap" rel="stylesheet">
<style>
  :root {
    --stage: #2b2b2b;
    --card-white: #ffffff;
    --brand-green: #4cb232;
    --band-green: #52b336;
    --band-green-dark: #46a52c;
    --ink: #3d3d3d;
    --ink-soft: #6a6a6a;
    --on-green: #ffffff;
    --rule-light: rgba(255,255,255,0.55);
  }
  * { margin: 0; padding: 0; box-sizing: border-box; }
  html, body {
    width: 1200px; height: 944px; overflow: hidden;
    background: var(--stage);
    font-family: "Open Sans", Arial, sans-serif;
  }
  .stage {
    width: 1200px; height: 944px;
    display: flex; flex-direction: column;
    align-items: center; justify-content: center; gap: 56px;
  }
  .card {
    width: 620px; height: 354px;
    border-radius: 26px;
    background: var(--card-white);
    overflow: hidden;
    position: relative;
  }
  .wordmark {
    display: flex; align-items: center; gap: 14px;
    color: var(--brand-green);
    font-weight: 400; letter-spacing: 0.5px;
  }
  .wordmark__square {
    width: 34px; height: 34px; background: var(--brand-green); flex: none;
  }
  /* Front */
  .card--front {
    display: flex; flex-direction: column;
    align-items: center; justify-content: center; gap: 44px;
  }
  .card--front .wordmark { font-size: 40px; }
  .card--front .web {
    font-size: 15px; color: var(--ink); letter-spacing: 1.2px;
  }
  /* Back */
  .card--back .brand-area {
    height: 150px;
    display: flex; align-items: center; justify-content: center;
    padding-top: 12px;
  }
  .card--back .wordmark { font-size: 34px; }
  .card--back .wordmark__square { width: 28px; height: 28px; }
  .band {
    position: absolute; left: 0; right: 0; bottom: 0; top: 160px;
    background: linear-gradient(180deg, var(--band-green) 0%, var(--band-green-dark) 100%);
    color: var(--on-green);
  }
  .band::before {
    content: ""; position: absolute; left: 8%; right: 8%; top: 0; height: 2px;
    background: linear-gradient(90deg, transparent, var(--rule-light), transparent);
  }
  .person {
    text-align: center; padding-top: 26px;
    font-size: 19px; font-weight: 600;
  }
  .person__role { font-size: 13px; font-weight: 400; margin-left: 4px; }
  .contacts {
    display: flex; justify-content: center; margin-top: 26px;
  }
  .contacts__col {
    display: flex; flex-direction: column; gap: 8px;
    padding: 4px 34px; font-size: 15px;
  }
  .contacts__col + .contacts__col { border-left: 1px solid var(--rule-light); }
  .contact { display: flex; align-items: center; gap: 12px; }
  .contact svg { width: 15px; height: 15px; flex: none; fill: var(--on-green); }
</style>
</head>
<body>
<main class="stage">
  <section class="card card--front" aria-label="Card front">
    <div class="wordmark"><span class="wordmark__square"></span><span>Stonefield Developments</span></div>
    <p class="web">www.stonefieldbuild.com</p>
  </section>

  <section class="card card--back" aria-label="Card back">
    <div class="brand-area">
      <div class="wordmark"><span class="wordmark__square"></span><span>Stonefield Developments</span></div>
    </div>
    <div class="band">
      <p class="person">Marcus Feld<span class="person__role">manager</span></p>
      <div class="contacts">
        <div class="contacts__col">
          <p class="contact">
            <svg viewBox="0 0 16 16" aria-label="Mobile"><path d="M4 1h3l1 4-2 1.5a9 9 0 0 0 3.5 3.5L11 8l4 1v3c0 1-1 2-2 2C7 14 2 9 2 3c0-1 1-2 2-2z"/></svg>
            555-010-2200
          </p>
          <p class="contact">
            <svg viewBox="0 0 16 16" aria-label="Fax"><rect x="4" y="1" width="8" height="5"/><rect x="1" y="6" width="14" height="6" rx="1"/><rect x="4" y="10" width="8" height="5" fill="#46a52c" stroke="#fff" stroke-width="1.2"/></svg>
            555-010-2201
          </p>
        </div>
        <div class="contacts__col">
          <p class="contact">
            <svg viewBox="0 0 16 16" aria-label="Email"><path d="M1 4h14v9H1z"/><path d="M1 4l7 5 7-5" fill="none" stroke="#46a52c" stroke-width="1.4"/></svg>
            info@stonefieldbuild.com
          </p>
          <p class="contact">
            <svg viewBox="0 0 16 16" aria-label="Website"><circle cx="8" cy="8" r="7"/></svg>
            www.stonefieldbuild.com
          </p>
        </div>
      </div>
    </div>
  </section>
</main>
</body>
</html>
```